Awesome business card design needed

We need a new business card design to go with our new logo.
We are a web development agency that specialises in highly complex back-end integrations as opposed to design, our customers are retailers, hotels, hospitals and any other organisation that has a large online marketing department.
Take a look at our website - www.brenoloft.com for some inspiration.
We want our new business cards to exude class, professionalism and style.
We are likely to choose a high-end card to print them on but we want the design of the card itself to really turn heads.
We have no specific colour requirements, the logo as you will see is a turquoise colour R89 G171 B167 #59aba7 but it can also be in white if you want to make the colour of the card something different.
The information on the card should be:
Name
Position
Tel
email
Potentially a double sided card could have our web address, twitter and FB links.

```html
<!DOCTYPE html>
<html lang="en">
<head>
<meta charset="utf-8">
<title>Brenoloft Business Card</title>
<link href="https://fonts.googleapis.com/css2?family=Open+Sans:wght@400;600;700&display=swap" rel="stylesheet">
<style>
  :root {
    --teal: #59aba7;
    --white: #ffffff;
    --ink: #4a4a4a;
    --grey-curve: #4b4d55;
    --rule: #c9c9c9;
    --backdrop: #eeeeec;
  }
  * { margin: 0; padding: 0; box-sizing: border-box; }
  html, body { width: 1200px; height: 720px; overflow: hidden; }
  body {
    background: var(--backdrop);
    font-family: "Open Sans", Arial, sans-serif;
    position: relative;
  }
  .card {
    position: absolute;
    top: 200px;
    width: 560px;
    height: 320px;
    overflow: hidden;
    box-shadow: 0 6px 18px rgba(0,0,0,0.18);
  }
  .card-front { left: 27px; background: var(--teal); }
  .card-back { left: 613px; background: var(--teal); }

  .front-swoop { position: absolute; inset: 0; }

  .brand-name {
    position: absolute;
    font-weight: 700;
    letter-spacing: 1px;
    line-height: 1;
  }
  .card-front .brand-name {
    left: 40px; top: 126px;
    font-size: 46px;
    color: var(--teal);
  }
  .divider {
    position: absolute;
    left: 318px; top: 36px;
    width: 1px; height: 150px;
    background: var(--rule);
  }
  .contact {
    position: absolute;
    left: 334px; top: 34px;
    color: var(--ink);
    font-size: 13px;
    line-height: 1.35;
  }
  .contact .person-name {
    font-size: 18px; font-weight: 700;
    color: var(--teal);
  }
  .contact .position { font-size: 11px; margin-bottom: 8px; }
  .contact .line { display: flex; align-items: center; gap: 8px; margin-bottom: 4px; }
  .contact .line svg { width: 12px; height: 12px; flex: none; }
  .contact .address { margin-top: 8px; font-size: 12px; line-height: 1.3; }
  .front-web {
    position: absolute;
    right: 24px; bottom: 44px;
    color: var(--white);
    font-size: 13px;
    letter-spacing: 1px;
  }

  .card-back .brand-name {
    left: 0; right: 0; top: 88px;
    text-align: center;
    font-size: 82px;
    color: var(--white);
  }
  .follow {
    position: absolute;
    left: 0; right: 0; top: 218px;
    display: flex; justify-content: center; align-items: center; gap: 10px;
    color: var(--white);
    font-size: 17px;
  }
  .social-mark {
    width: 30px; height: 30px;
    border-radius: 4px;
    background: var(--white);
    opacity: 0.9;
  }
  .back-web {
    position: absolute;
    left: 0; right: 0; top: 262px;
    text-align: center;
    color: var(--white);
    font-size: 17px;
    letter-spacing: 2px;
  }
</style>
</head>
<body>
  <section class="card card-front">
    <svg class="front-swoop" viewBox="0 0 560 320" aria-hidden="true">
      <defs>
        <linearGradient id="curve-fade" x1="0" y1="0" x2="560" y2="0" gradientUnits="userSpaceOnUse">
          <stop offset="0" stop-color="var(--grey-curve)" stop-opacity="1"/>
          <stop offset="0.45" stop-color="var(--grey-curve)" stop-opacity="1"/>
          <stop offset="0.75" stop-color="var(--grey-curve)" stop-opacity="0"/>
        </linearGradient>
      </defs>
      <path d="M0,36 C28,14 60,4 96,2" fill="none" stroke="var(--grey-curve)" stroke-width="3"/>
      <path d="M0,298 C200,306 400,236 560,166" fill="none" stroke="url(#curve-fade)" stroke-width="5"/>
      <path d="M0,30 C28,10 58,0 92,0 H560 V156 C400,228 200,292 0,288 Z" fill="var(--white)"/>
    </svg>
    <div class="brand-name">brenoloft</div>
    <div class="divider"></div>
    <div class="contact">
      <div class="person-name">Your Name</div>
      <div class="position">Position</div>
      <div class="line">
        <svg viewBox="0 0 24 24"><path d="M6.6 10.8a15 15 0 0 0 6.6 6.6l2.2-2.2c.3-.3.7-.4 1-.2 1.1.4 2.3.6 3.6.6.6 0 1 .4 1 1V20c0 .6-.4 1-1 1A17 17 0 0 1 3 4c0-.6.4-1 1-1h3.5c.6 0 1 .4 1 1 0 1.3.2 2.5.6 3.6.1.3 0 .7-.2 1z" fill="var(--ink)"/></svg>
        <span>123-456-7890</span>
      </div>
      <div class="line">
        <svg viewBox="0 0 24 24"><rect x="2" y="5" width="20" height="14" rx="2" fill="var(--ink)"/><path d="M3 6l9 7 9-7" fill="none" stroke="var(--white)" stroke-width="1.6"/></svg>
        <span>info@brenoloft.com</span>
      </div>
      <div class="address">Street Name, City Name<br>State Zip Code</div>
    </div>
    <div class="front-web">www.brenoloft.com</div>
  </section>

  <section class="card card-back">
    <div class="brand-name">brenoloft</div>
    <div class="follow">
      <span>Follow Us On:</span>
      <span class="social-mark" role="img" aria-label="Social network link"></span>
      <span class="social-mark" role="img" aria-label="Social network link"></span>
    </div>
    <div class="back-web">www.brenoloft.com</div>
  </section>
</body>
</html>
```